Upmarket Dessert Lounge needs a Business Card Design

We are an upmarket dessert lounge needing a business card to match our image.

We want something that is simple yet beautiful, feminine, classy, sophisticated and elegant. We want it to stand out and don't mind if it is bold.

The design should include our logo and colours of red or maroon with gold highlights. We don't mind if black is used.

Marlow & Quince

Target Market(s)

For those who like to indulge or treat themselves and give in to their temptations on good quality desserts.

Industry/Entity Type

Business

Requirements
Must have
• Must include our logo and our name

Marlow & Quince

M & Q

```html
<!DOCTYPE html>
<html lang="en">
<head>
<meta charset="utf-8">
<title>Marlow &amp; Quince — Business Card</title>
<link rel="stylesheet" href="https://fonts.googleapis.com/css2?family=Source+Sans+3:wght@400;600;700&display=swap">
<style>
  :root {
    --backdrop: #d9d9db;
    --card: #ffffff;
    --maroon: #7a1416;
    --gold: #e9c88f;
    --ink: #333333;
    --ink-strong: #2b2b2b;
    --shadow: rgba(0, 0, 0, 0.28);
  }
  html, body {
    margin: 0;
    padding: 0;
    overflow: hidden;
  }
  body {
    width: 956px;
    height: 1200px;
    background: var(--backdrop);
    position: relative;
    font-family: "Source Sans 3", "Myriad Pro", Arial, sans-serif;
    color: var(--ink);
  }
  .card {
    position: absolute;
    width: 798px;
    height: 456px;
    background: var(--card);
    border-radius: 30px;
    box-shadow: 6px 8px 14px var(--shadow);
  }
  .card--front { left: 79px; top: 70px; }
  .card--back  { left: 74px; top: 632px; }

  .brand-mark {
    position: absolute;
    display: flex;
    align-items: center;
    justify-content: center;
    gap: 16px;
    color: var(--maroon);
    font-weight: 600;
    white-space: nowrap;
    line-height: 1;
  }
  .brand-mark__dot {
    flex: none;
    border-radius: 50%;
    background: var(--gold);
  }
  .card--front .brand-mark {
    left: 60px;
    top: 136px;
    width: 320px;
    height: 70px;
    font-size: 64px;
  }
  .card--front .brand-mark__dot { width: 22px; height: 22px; }
  .card--back .brand-mark {
    left: 0;
    top: 196px;
    width: 798px;
    height: 60px;
    font-size: 48px;
    letter-spacing: 1px;
  }
  .card--back .brand-mark__dot { width: 18px; height: 18px; }

  .contact {
    position: absolute;
    left: 425px;
    top: 66px;
  }
  .contact__name {
    font-size: 26px;
    font-weight: 700;
    color: var(--ink-strong);
    line-height: 26px;
  }
  .contact__role {
    font-size: 26px;
    font-weight: 400;
    letter-spacing: 0.5px;
    line-height: 26px;
    margin-bottom: 18px;
  }
  .contact__list {
    list-style: none;
    margin: 0;
    padding: 0;
    font-size: 22px;
  }
  .contact__list li { line-height: 30px; }
  .contact__list li.gap { margin-top: 7px; }
  .contact__label { font-weight: 700; }

  .address {
    position: absolute;
    left: 0;
    width: 798px;
    top: 399px;
    line-height: 30px;
    text-align: center;
    font-size: 26.5px;
  }
</style>
</head>
<body>
  <section class="card card--front">
    <div class="brand-mark"><span class="brand-mark__dot"></span>M &amp; Q</div>
    <div class="contact">
      <div class="contact__name">Your Name</div>
      <div class="contact__role">Designation</div>
      <ul class="contact__list">
        <li><span class="contact__label">p</span> : 123-456-7890</li>
        <li><span class="contact__label">c</span> : 123-456-7890</li>
        <li><span class="contact__label">f</span> : 123-456-7890</li>
        <li class="gap"><span class="contact__label">e</span> : name@yourwebsite.com</li>
        <li><span class="contact__label">w</span> : www.marlow&amp;quince.com</li>
      </ul>
    </div>
    <div class="address">0000, Street Name, City Name, Country Code.</div>
  </section>

  <section class="card card--back">
    <div class="brand-mark"><span class="brand-mark__dot"></span>Marlow &amp; Quince</div>
  </section>
</body>
</html>
```